business card for a massage therapy practice named 'Cedar and Willow Massage Studio'

I really need a trendy, yet easy on the eyes business card to complement my logo. Ideally with some gold or rose gold foil work.

My uploaded file of the logo I have in horizontal but I have a vertical version as well. Another color that is used in the website is a blush pink here and there. I'd like to see some trendy tropical leaves in the design.

```html
<!DOCTYPE html>
<html lang="en">
<head>
<meta charset="utf-8">
<title>Cedar and Willow Massage Studio — Business Card</title>
<link href="https://fonts.googleapis.com/css2?family=Oswald:wght@500&family=Work+Sans:wght@400&display=swap" rel="stylesheet">
<style>
  :root {
    --backdrop: #2b2b2c;
    --card: #1b1b1c;
    --card-edge: #242425;
    --gold: #b39a6c;
    --ink: #f2f2f0;
    --muted: #9a9a98;
  }
  * { margin: 0; padding: 0; box-sizing: border-box; }
  html, body { width: 1200px; height: 900px; overflow: hidden; }
  body {
    background: var(--backdrop);
    display: flex;
    flex-direction: column;
    align-items: center;
    justify-content: center;
    gap: 40px;
    font-family: "Work Sans", sans-serif;
    color: var(--ink);
  }
  .card {
    width: 700px;
    height: 400px;
    background: linear-gradient(160deg, var(--card-edge), var(--card) 60%);
    box-shadow: 0 18px 40px rgba(0,0,0,0.45);
    position: relative;
  }
  /* Front */
  .card-front {
    display: flex;
    align-items: center;
    justify-content: center;
  }
  .brand {
    display: flex;
    align-items: center;
    gap: 18px;
  }
  .brand-dot {
    width: 34px;
    height: 34px;
    border-radius: 50%;
    background: var(--gold);
  }
  .brand-name {
    font-family: "Work Sans", sans-serif;
    font-weight: 400;
    font-size: 32px;
    letter-spacing: 0.5px;
    color: var(--ink);
  }
  /* Back */
  .holder {
    position: absolute;
    left: 70px;
    top: 132px;
    display: flex;
    align-items: center;
  }
  .holder-name {
    font-family: "Oswald", sans-serif;
    font-weight: 500;
    font-size: 42px;
    letter-spacing: 1px;
    color: var(--gold);
    text-transform: uppercase;
    white-space: nowrap;
  }
  .divider {
    width: 2px;
    height: 62px;
    background: var(--ink);
    margin: 0 34px 0 30px;
  }
  .contact-list {
    list-style: none;
    font-size: 17px;
    line-height: 1.45;
  }
  .contact-list li {
    display: flex;
    align-items: center;
    gap: 10px;
  }
  .contact-icon {
    width: 12px;
    height: 12px;
    flex: none;
  }
  .address {
    position: absolute;
    left: 0;
    right: 0;
    bottom: 72px;
    text-align: center;
    font-size: 17px;
    letter-spacing: 0.3px;
  }
</style>
</head>
<body>

  <section class="card card-front" aria-label="Card front">
    <div class="brand">
      <span class="brand-dot"></span>
      <span class="brand-name">Cedar and Willow Massage Studio</span>
    </div>
  </section>

  <section class="card card-back" aria-label="Card back">
    <div class="holder">
      <h1 class="holder-name">Marisol Vega</h1>
      <span class="divider"></span>
      <ul class="contact-list">
        <li>
          <svg class="contact-icon" viewBox="0 0 12 12" fill="none" stroke="#9a9a98" stroke-width="1.2">
            <path d="M3 1 L5 3.5 L3.8 5 Q5 7.5 7 8.2 L8.5 7 L11 9 L9.6 11 Q4 10.5 1 3 Z"/>
          </svg>
          (555) 214-0387
        </li>
        <li>
          <svg class="contact-icon" viewBox="0 0 12 12" fill="none" stroke="#9a9a98" stroke-width="1.2">
            <rect x="1" y="2.5" width="10" height="7"/>
            <path d="M1 2.5 L6 6.5 L11 2.5"/>
          </svg>
          hello@cedarandwillow.com
        </li>
        <li>
          <svg class="contact-icon" viewBox="0 0 12 12" fill="none" stroke="#9a9a98" stroke-width="1.1">
            <circle cx="6" cy="6" r="5"/>
            <ellipse cx="6" cy="6" rx="2.2" ry="5"/>
            <path d="M1 6 H11"/>
          </svg>
          www.cedarandwillow.com
        </li>
      </ul>
    </div>
    <p class="address">418 Alder St. suite 210, Fairview, CA 95010</p>
  </section>

</body>
</html>
```